Website visual upgrade

I am seeking expressions of interest for the updating the visuals of my website www.kelvastaffing.net
I am basically seeking a simple,bold and visually strong graphic makeover.using existing or shortly to be modified text.

```html
<!DOCTYPE html>
<html lang="en">
<head>
<meta charset="utf-8">
<title>Kelva Staffing</title>
<link rel="stylesheet" href="https://fonts.googleapis.com/css2?family=Lato:wght@400;700&family=Arimo:wght@400;700&display=swap">
<style>
:root{
  --red:#c8173a;
  --crimson:#d0155a;
  --ink:#1a1a1a;
  --dark:#222;
  --grey:#6b6b6b;
  --light:#f3f3f3;
  --line:#cfcfcf;
  --white:#fff;
  --blue:#1f8fd6;
}
*{margin:0;padding:0;box-sizing:border-box}
html,body{width:1200px;height:949px;overflow:hidden;background:var(--white)}
body{position:relative;font-family:Arimo,Arial,sans-serif;color:var(--ink)}
.abs{position:absolute}

/* top bar */
.topbar{left:0;top:0;width:1200px;height:26px;border-bottom:1px solid var(--line);background:var(--white)}
.tab{top:0;height:26px;background:#eee;border:1px solid var(--line);border-top:0;font:700 12px Lato,sans-serif;color:#555;display:flex;align-items:center;justify-content:center}
.field{top:4px;height:15px;border:1px solid #bbb;border-radius:2px;background:#fff;font-size:7px;color:#333;padding-left:5px;display:flex;align-items:center}
.field span{position:absolute;right:2px;top:2px;height:10px;padding:0 4px;background:#777;color:#fff;border-radius:2px;font-size:6px;line-height:10px}
.btn-top{top:4px;height:15px;border-radius:2px;font:400 9px Lato,sans-serif;display:flex;align-items:center;justify-content:center}
.btn-login{left:839px;width:51px;background:#ddd;border:1px solid #aaa;color:#333}
.btn-signup{left:898px;width:51px;background:var(--blue);color:#fff}

/* header */
.header{left:0;top:52px;width:1200px;height:50px;background:var(--red)}
.brand{left:250px;top:52px;width:254px;height:50px;background:var(--white);display:flex;align-items:center;gap:10px;padding-left:12px}
.brand-mark{width:16px;height:16px;background:var(--red)}
.brand-name{font:700 24px Lato,sans-serif;color:var(--red)}
.nav{left:512px;top:52px;height:50px;display:flex;align-items:center;gap:6px;font:700 12px Lato,sans-serif;color:var(--white)}
.nav .sep{font-size:8px}
.nav .active{background:#000;padding:2px 4px}

/* hero */
.hero{left:0;top:102px;width:1200px;height:293px;background:linear-gradient(180deg,#3a3a3a 0%,#777 30%,#2a2a2a 65%,#444 100%)}
.arrow{top:225px;width:48px;height:48px;border-radius:50%;background:var(--white);display:flex;align-items:center;justify-content:center}
.hero-title{left:0;top:326px;width:1200px;text-align:center;font:700 26px Lato,sans-serif;color:#fff;text-shadow:0 0 2px var(--crimson)}
.hero-sub{left:0;top:353px;width:1200px;text-align:center;font:700 21px Lato,sans-serif;color:var(--crimson)}

/* cards */
.features{left:0;top:395px;width:1200px;height:255px;background:var(--light)}
.card{top:424px;width:153px;height:196px;background:var(--white);border-left:5px solid var(--dark);box-shadow:0 5px 6px rgba(0,0,0,.18)}
.card-head{height:28px;background:var(--red);color:#fff;font:400 18px Lato,sans-serif;padding-left:9px;line-height:28px;position:relative}
.card-icon{position:absolute;right:0;top:0;width:28px;height:28px;background:var(--dark);display:flex;align-items:center;justify-content:center}
.card-body{padding:7px 8px 0 8px}
.card-lead{font:700 9.6px/12px Arimo,Arial,sans-serif;margin-bottom:12px}
.card-text{font:400 8.4px/10.3px Arimo,Arial,sans-serif}
.read-more{position:absolute;left:8px;top:168px;width:68px;height:16px;background:#ddd;border-bottom:2px solid #aaa;font:700 8.4px Arimo,Arial,sans-serif;display:flex;align-items:center;justify-content:center}
.country-list{list-style:none;padding:5px 0 0 8px;font:400 8.4px Arimo,Arial,sans-serif}
.country-list li{height:14.9px}
.country-list li::before{content:"• ";color:var(--red)}

/* testimonials */
.testimonials{left:0;top:650px;width:1200px;height:140px;background:#0a0a0a;color:#fff;text-align:center}
.testimonials h2{margin-top:16px;font:700 27px Lato,sans-serif}
.testimonials p{width:680px;margin:12px auto 0;font:400 8.6px/15.2px Arimo,Arial,sans-serif}

/* footer */
.footer-nav{left:250px;top:790px;height:28px;display:flex;align-items:center;gap:26px;font:400 12px Lato,sans-serif;color:#444}
.footer-rule{left:0;top:817px;width:1200px;height:1px;background:var(--line)}
.search{left:826px;top:797px;width:123px;height:14px;border:1px solid #bbb;border-radius:2px;font-size:7px;padding-left:5px;line-height:12px;color:#444}
.search span{position:absolute;right:1px;top:1px;width:12px;height:10px;background:#666;border-radius:2px}
.crumbs{left:250px;top:834px;font:400 8.6px Arimo,Arial,sans-serif;display:flex;gap:5px}
.copyright{left:250px;top:854px;font:400 8.6px Arimo,Arial,sans-serif}
.support-title{left:797px;top:824px;font:400 18px Lato,sans-serif;color:#222}
.badge-a{left:797px;top:858px;width:53px;height:38px;background:#111}
.badge-b{left:864px;top:862px;width:85px;height:32px;background:#e9eef4;border-radius:4px}
</style>
</head>
<body>

<div class="abs topbar"></div>
<div class="abs tab" style="left:250px;width:66px">CLIENT</div>
<div class="abs tab" style="left:316px;width:90px">JOB SEEKER</div>
<div class="abs field" style="left:576px;width:122px">Email<span>?</span></div>
<div class="abs field" style="left:707px;width:123px">Password<span>forgot?</span></div>
<div class="abs btn-top btn-login">Log in</div>
<div class="abs btn-top btn-signup">Sign up</div>

<div class="abs header"></div>
<div class="abs brand"><span class="brand-mark"></span><span class="brand-name">Kelva Staffing</span></div>
<nav class="abs nav">
  <span class="active">Home</span><span class="sep">•</span>
  <span>Migration assistance</span><span class="sep">•</span>
  <span>Job seeker</span><span class="sep">•</span>
  <span>Useful links</span><span class="sep">•</span>
  <span>Support</span><span class="sep">•</span>
  <span>Contact us</span>
</nav>

<div class="abs hero" role="img" aria-label="Black and white night photograph of a city skyline over water"></div>
<div class="abs arrow" style="left:250px"><svg width="14" height="20" viewBox="0 0 14 20"><path d="M11 2 3 10l8 8" fill="none" stroke="#c8173a" stroke-width="3"/></svg></div>
<div class="abs arrow" style="left:901px"><svg width="14" height="20" viewBox="0 0 14 20"><path d="M3 2l8 8-8 8" fill="none" stroke="#c8173a" stroke-width="3"/></svg></div>
<div class="abs hero-title">We are Executive search and selection specialists</div>
<div class="abs hero-sub">We work exclusively with our clients</div>

<div class="abs features"></div>

<section class="abs card" style="left:250px">
  <div class="card-head">Who we are<span class="card-icon"><svg width="18" height="18" viewBox="0 0 18 18" fill="none" stroke="#fff" stroke-width="1.3"><circle cx="9" cy="6" r="4"/><path d="M2 17c0-4 3-6 7-6s7 2 7 6z"/></svg></span></div>
  <div class="card-body">
    <p class="card-lead">We have recruited for over 400 leading companies</p>
    <p class="card-text">Lorem Ipsum is simply dummy text of the printing and typesetting industry. Lorem Ipsum has been the industry's standard dummy text ever since the 1500s, when an unknown printer took a galley of type and scrambled it to make a type specimen book.</p>
  </div>
  <div class="read-more">Read More</div>
</section>

<section class="abs card" style="left:431px">
  <div class="card-head">What we do<span class="card-icon"><svg width="16" height="18" viewBox="0 0 16 18" fill="none" stroke="#fff" stroke-width="1.3"><rect x="3" y="1" width="11" height="16"/><path d="M6 5h5M6 8h5M6 11h5M1 4v13h10"/></svg></span></div>
  <div class="card-body">
    <p class="card-lead">We are a specialist recruiter to the Health sector.</p>
    <p class="card-text">Lorem Ipsum is simply dummy text of the printing and typesetting industry. Lorem Ipsum has been the industry's standard dummy text ever since the 1500s, when an unknown printer took a galley of type and scrambled it to make a type specimen book.</p>
  </div>
  <div class="read-more">Read More</div>
</section>

<section class="abs card" style="left:613px">
  <div class="card-head">Our Approach<span class="card-icon"><svg width="20" height="20" viewBox="0 0 20 20" fill="none" stroke="#fff" stroke-width="1.3"><circle cx="10" cy="10" r="3"/><circle cx="10" cy="10" r="6.5" stroke-dasharray="3 2"/></svg></span></div>
  <div class="card-body">
    <p class="card-lead">Make you business<br>the best it can be</p>
    <p class="card-text">Lorem Ipsum is simply dummy text of the printing and typesetting industry. Lorem Ipsum has been the industry's standard dummy text ever since the 1500s, when an unknown printer took a galley of type and scrambled it to make a type specimen book.</p>
  </div>
  <div class="read-more">Read More</div>
</section>

<section class="abs card" style="left:797px">
  <div class="card-head">Job Seeker's from</div>
  <ul class="country-list">
    <li>United Kingdom</li><li>Middle East</li><li>Zimbabwe</li><li>Malaysia</li><li>Singapore</li>
    <li>China</li><li>Philippines</li><li>New Zealand</li><li>Sounth Africa</li><li>Botswana</li>
  </ul>
</section>

<section class="abs testimonials" role="img" aria-label="Dark band with a faint dotted world map behind client testimonials">
  <h2>Client’s Testimonials</h2>
  <p>Lorem Ipsum is simply dummy text of the printing and typesetting industry. Lorem Ipsum has been the industry's standard dummy text ever since the 1500s, when an unknown printer took a galley of type and scrambled it to make a type specimen book. It has survived not only five centuries, but also the leap into electronic typesetting, remaining essentially unchanged. It was popularised in the 1960s with the release of Lettersheet sheets containing Lorem Ipsum passages, and more recently with desktop publishing software like Pagewright including versions of Lorem Ipsum.</p>
</section>

<nav class="abs footer-nav">
  <span>Help</span><span>Contact</span><span>Fees</span><span>About</span><span>Blog</span><span>Jobs</span><span>Sitemap</span><span>Feedback</span>
</nav>
<div class="abs search">Search<span></span></div>
<div class="abs footer-rule"></div>

<div class="abs crumbs">
  <span>Home</span>•<span>Who we are</span>•<span>Our Approach</span>•<span>What we do</span>•<span>Migration assistance</span>•<span>Job seeker</span>•<span>Useful links</span>•<span>Support</span>•<span>Contact us</span>
</div>
<div class="abs copyright">© Kelva Partners 2013</div>

<div class="abs support-title">We Proudly Support</div>
<div class="abs badge-a" aria-label="Partner badge"></div>
<div class="abs badge-b" aria-label="Partner badge"></div>

</body>
</html>
```